Financial Services General Marketing Brochure

Need a brochure to help recipients understand what makes BWC unique and the services that we offer. Must match look/feel of website https://brightwellcustody.example Layouts should make it easy to read the content - content should not be crammed into a traditional size/layout. Please see attached creative brief for specifics.

Target Market(s)

Financial advisors and mature couples looking for trustee services.

Industry/Entity Type

Financial Service

Colors
34a7d8
ffc214

Requirements
Must have
• See Creative Brief

```html
<!DOCTYPE html>
<html lang="en">
<head>
<meta charset="utf-8">
<title>BWC Brochure – Inside Spread</title>
<link rel="stylesheet" href="https://fonts.googleapis.com/css2?family=Noto+Serif:ital,wght@0,400;1,400&family=Open+Sans:wght@400;600&display=swap">
<style>
  :root{
    --page:#ffffff;
    --slate:#56728f;
    --slate-band:#5b7b9b;
    --sand:#f3ece3;
    --cream:#fcf9f3;
    --ring:#c9b49c;
    --gold:#e5a63a;
    --heading:#4f6c8a;
    --body:#555a60;
    --rule:#d6d6d6;
  }
  *{box-sizing:border-box;margin:0;padding:0}
  html,body{width:1200px;height:1000px;overflow:hidden;background:var(--page)}
  body{position:relative;font-family:"Open Sans",Arial,sans-serif}
  h2,h3{font-weight:400}
  .spread{position:absolute;left:0;top:200px;width:1200px;height:600px;border:1px solid var(--rule)}
  .fold{position:absolute;left:599px;top:180px;height:640px;border-left:2px dashed #cfcfcf}

  /* left panel */
  .panel-intro{position:absolute;left:0;top:0;width:300px;height:600px}
  .intro-photo{height:165px;background:linear-gradient(120deg,#c9a47a 0%,#3e5473 40%,#6d7f96 70%,#2e3c52 100%)}
  .intro-body{height:435px;background:var(--slate);color:#fff;padding:38px 36px 0 42px;font-family:"Noto Serif",Georgia,serif;font-size:10.6px;line-height:17.5px;letter-spacing:-0.1px}
  .intro-body p{margin-bottom:17px}
  .dropcap{float:left;font-size:54px;line-height:44px;margin:2px 4px 0 0}
  .signature{position:absolute;left:94px;top:535px;font-size:13px;line-height:18px;color:#fff}
  .signature strong{font-weight:600}

  /* middle panel */
  .panel-unique{position:absolute;left:300px;top:0;width:300px;height:600px}
  .band-sand{position:absolute;left:0;top:33px;width:300px;height:65px;background:var(--sand);display:flex;align-items:center;justify-content:center;font-family:"Noto Serif",Georgia,serif;font-size:20px;color:var(--heading)}
  .traits{position:absolute;left:25px;top:132px;width:250px}
  .trait h3{font-family:"Noto Serif",Georgia,serif;font-style:italic;color:var(--gold);font-size:14.5px;margin-bottom:4px}
  .trait p{font-size:10.6px;line-height:15px;color:var(--body);margin-bottom:13px}

  /* right panel */
  .panel-team{position:absolute;left:600px;top:0;width:599px;height:598px;background:linear-gradient(90deg,#fff 0%,var(--cream) 100%)}
  .band-slate{position:absolute;left:0;top:33px;width:599px;height:66px;background:var(--slate-band);color:#fff;text-align:center;font-family:"Noto Serif",Georgia,serif;font-size:20px;line-height:25px;padding-top:7px}
  .team-diagram{position:absolute;left:0;top:0}
  .node-label{font-family:"Noto Serif",Georgia,serif;fill:var(--heading);font-size:18px;text-anchor:middle}
  .node-small{font-family:"Open Sans",Arial,sans-serif;fill:var(--body);font-size:7.5px;text-anchor:middle}
</style>
</head>
<body>
<div class="fold"></div>
<main class="spread">
  <section class="panel-intro">
    <div class="intro-photo" role="img" aria-label="Photo of a smiling advisor in a blue blazer meeting with a client"></div>
    <div class="intro-body">
      <p><span class="dropcap">W</span>e understand that wealth and families is very complex. As families try to transfer wealth it can be an incredible blessing or, if done improperly, can be incredibly destructive. Often a neutral third party is needed to come alongside the family's advisory team to provide guidance as families go through their wealth transition.</p>
      <p>Our relational focus, and open counsel approach, helps families to successfully navigate through the complexities of wealth, family and trusts. We believe a family "legacy" is about more than just money.</p>
    </div>
    <div class="signature"><strong>Daniel Rowe, J.D.</strong><br>Founding Principal</div>
  </section>

  <section class="panel-unique">
    <h2 class="band-sand">What Makes BWC Unique</h2>
    <div class="traits">
      <div class="trait"><h3>Responsive</h3><p>The family deals directly with decision makers instead of being subject to committees with whom the family may never have the opportunity to interact or engage.</p></div>
      <div class="trait"><h3>Family Focus</h3><p>We help families successfully navigate the complexities of family wealth, not just perform trust administration.</p></div>
      <div class="trait"><h3>Independent</h3><p>To avoid any conflicts of interest, we have no formal affiliations with wealth management firms or financial advisory practices.</p></div>
      <div class="trait"><h3>Customized</h3><p>Together we develop a customized approach that will best suit the family's needs.</p></div>
      <div class="trait"><h3>Collaborative</h3><p>We work collaboratively with the family's team of trusted professionals.</p></div>
    </div>
  </section>

  <section class="panel-team">
    <h2 class="band-slate">Brightwell Custody Group<br>Client/Family Centered Team</h2>
    <svg class="team-diagram" width="599" height="598" viewBox="600 200 599 598">
      <defs>
        <linearGradient id="photoWarm" x1="0" y1="0" x2="1" y2="1"><stop offset="0" stop-color="#e9dccd"/><stop offset="1" stop-color="#c8a98a"/></linearGradient>
        <linearGradient id="photoLight" x1="0" y1="0" x2="1" y2="1"><stop offset="0" stop-color="#f4f1ee"/><stop offset="1" stop-color="#d9cbbd"/></linearGradient>
      </defs>
      <g stroke="var(--ring)" stroke-width="3">
        <line x1="746" y1="496" x2="812" y2="496"/>
        <line x1="988" y1="496" x2="1053" y2="496"/>
        <line x1="855" y1="577" x2="806" y2="626"/>
        <line x1="945" y1="577" x2="997" y2="626"/>
      </g>
      <g stroke="var(--ring)" stroke-width="3">
        <circle cx="817" cy="373" r="59" fill="url(#photoWarm)" role="img" aria-label="Portrait photo of a smiling woman"/>
        <circle cx="985" cy="373" r="59" fill="url(#photoLight)" role="img" aria-label="Photo of two smiling children"/>
        <polygon points="810,497 855,418 945,418 990,497 945,577 855,577" fill="url(#photoLight)" role="img" aria-label="Photo of a smiling senior couple"/>
        <circle cx="686" cy="496" r="59" fill="var(--sand)"/>
        <circle cx="1113" cy="496" r="59" fill="var(--sand)"/>
        <circle cx="763" cy="669" r="59" fill="var(--sand)"/>
        <circle cx="1040" cy="669" r="59" fill="var(--sand)"/>
        <circle cx="901" cy="714" r="59" fill="var(--sand)"/>
      </g>
      <text class="node-label" x="686" y="502">Attorney</text>
      <text class="node-label" x="1113" y="502">Accountant</text>
      <text class="node-label" x="763" y="675">Financial</text>
      <text class="node-label" x="1040" y="675">Trustee</text>
      <circle cx="1040" cy="700" r="8" fill="var(--gold)"/>
      <text class="node-label" x="901" y="691" style="font-size:12.5px">Human Capital</text>
      <text class="node-label" x="901" y="707" style="font-size:12.5px">Resources</text>
      <text class="node-small" x="901" y="725">Legacy Development</text>
      <text class="node-small" x="901" y="736">Health Care Management</text>
      <text class="node-small" x="901" y="747">Philanthropic Services</text>
      <text class="node-small" x="901" y="758">Life Coaching</text>
    </svg>
  </section>
</main>
</body>
</html>
```